Vantro cards

I am in the auto motive, transportation business I would like a business card that is Something cool, modern edgy, having to do with car culture. I offer towing service for high and exotic cars. I also provide towing for collisions and car accidents. I offer open and enclosed transport nationwide.

Target Market(s)

Car culture people high end auto collectors

Industry/Entity Type

Towing car carrier

Contact Information for Business Card

My company colors black yellow and silver

Font styles to use
Serif

```html
<!DOCTYPE html>
<html lang="en">
<head>
<meta charset="utf-8">
<title>Vantro Transportation – Business Cards</title>
<link rel="stylesheet" href="https://fonts.googleapis.com/css2?family=Montserrat:wght@400;500;700;800&display=swap">
<style>
  :root {
    --ink: #0b0b0b;
    --paper: #ffffff;
    --yellow: #f7dc4a;
    --yellow-deep: #f2d230;
    --silver-light: #f4f4f4;
    --silver-mid: #bdbdbd;
    --silver-dark: #8a8a8a;
    --ghost: #ececec;
    --stage: #e7e5e1;
    --light-text: #f2f2f2;
  }
  * { margin: 0; padding: 0; box-sizing: border-box; }
  html, body {
    width: 900px; height: 1200px; overflow: hidden;
    background: var(--stage);
    font-family: "Montserrat", sans-serif;
  }
  .canvas { position: relative; width: 900px; height: 1200px; }

  .card {
    position: absolute; left: 80px; width: 742px; height: 444px;
    border-radius: 28px; overflow: hidden;
    box-shadow: 0 6px 14px rgba(0,0,0,0.25);
  }

  /* Front */
  .card-front { top: 132px; background: var(--paper); }
  .brand-mark {
    position: absolute; left: 42px; top: 62px; width: 190px;
    display: flex; flex-direction: column; align-items: center; gap: 6px;
    color: var(--ink); font-weight: 800; text-align: center;
  }
  .brand-square { width: 26px; height: 26px; background: var(--yellow); margin-bottom: 6px; }
  .brand-name { font-size: 46px; line-height: 1; letter-spacing: 1px; }
  .brand-sub { font-size: 15px; letter-spacing: 1px; }
  .ghost-name {
    position: absolute; left: 320px; top: 120px;
    font-size: 110px; font-weight: 800; color: var(--ghost); letter-spacing: 2px;
  }
  .front-graphics { position: absolute; left: 0; top: 0; }
  .person {
    position: absolute; left: 28px; top: 273px; color: var(--ink);
  }
  .person-name { font-size: 26px; font-weight: 700; line-height: 1.1; }
  .person-role { font-size: 15px; font-weight: 400; margin-top: 2px; }
  .contact-list {
    position: absolute; left: 28px; top: 350px; list-style: none;
    color: var(--light-text); font-size: 16.5px; line-height: 21.5px;
  }
  .contact-list li { display: flex; align-items: center; gap: 12px; }
  .contact-list svg { width: 12px; height: 12px; fill: var(--yellow); flex: none; }
  .address {
    position: absolute; left: 502px; top: 373px;
    border-left: 2px solid var(--yellow); padding-left: 19px;
    color: var(--light-text); font-size: 16.5px; line-height: 21.5px;
  }

  /* Back */
  .card-back {
    top: 638px;
    background:
      radial-gradient(ellipse at 50% 45%, rgba(255,255,255,0.9) 0%, rgba(255,255,255,0) 55%),
      conic-gradient(from 0deg at 50% 45%, var(--silver-mid), var(--silver-light), var(--silver-dark), var(--silver-light), var(--silver-mid), var(--silver-light), var(--silver-dark), var(--silver-light), var(--silver-mid));
  }
  .back-mark {
    position: absolute; left: 0; right: 0; top: 140px;
    display: flex; flex-direction: column; align-items: center; gap: 10px;
    color: var(--ink); font-weight: 800;
  }
  .back-mark .brand-square { width: 32px; height: 32px; }
  .back-mark .brand-name { font-size: 64px; }
  .back-mark .brand-sub { font-size: 20px; }
  .accent-line { position: absolute; left: 0; right: 0; top: 364px; height: 6px; background: var(--yellow); }
  .back-band {
    position: absolute; left: 0; right: 0; top: 382px; bottom: 0;
    background: var(--ink); color: var(--light-text);
    display: flex; align-items: center; justify-content: center;
    font-size: 16px; letter-spacing: 0.3px; padding-bottom: 6px;
  }
</style>
</head>
<body>
<main class="canvas">

  <section class="card card-front" aria-label="Business card front">
    <div class="ghost-name" aria-hidden="true">VANTRO</div>
    <div class="brand-mark">
      <span class="brand-square"></span>
      <span class="brand-name">VANTRO</span>
      <span class="brand-sub">TRANSPORTATION</span>
    </div>

    <svg class="front-graphics" width="742" height="444" viewBox="0 0 742 444" aria-hidden="true">
      <polygon points="0,268 236,268 262,326 0,326" fill="var(--yellow)"/>
      <polygon points="260,304 742,304 742,316 266,316" fill="var(--ink)"/>
      <rect x="0" y="328" width="742" height="116" fill="var(--ink)"/>
    </svg>

    <div class="person">
      <div class="person-name">Dario Kessler</div>
      <div class="person-role">Owner</div>
    </div>

    <ul class="contact-list">
      <li><svg viewBox="0 0 12 12"><path d="M1 4 Q6 0 11 4 L9 6 L8 4.5 L4 4.5 L3 6 Z M2 7 H10 V11 H2 Z"/></svg>(555) 214-3098</li>
      <li><svg viewBox="0 0 12 12"><path d="M0 2 H12 V10 H0 Z" /></svg>info@vantrotransportation.com</li>
      <li><svg viewBox="0 0 12 12"><circle cx="6" cy="6" r="5.5"/></svg>www.vantrotransportation.com</li>
    </ul>

    <div class="address">48 Ridge Avenue<br>Alderton, PA 17500</div>
  </section>

  <section class="card card-back" aria-label="Business card back">
    <div class="back-mark">
      <span class="brand-square"></span>
      <span class="brand-name">VANTRO</span>
      <span class="brand-sub">TRANSPORTATION</span>
    </div>
    <div class="accent-line"></div>
    <div class="back-band">www.vantrotransportation</div>
  </section>

</main>
</body>
</html>
```